BrambleForge Development Studio Website

We'd like to create a brand new website for our company, so we can display our portfolio, our team, and our general approach to the app development work that we do. We've attached the website content + portfolio images for your convenience.

Our company is focused on substance over glamour, so we want our website to represent that mentality. We need something simple, and clean. We're open to both minimalist designs and as well as bolder designs.

Target Market(s)

Businesses: Startups and established companies

Coding

Coded - Design and coding required

Number of Pages Required

2 page

Font styles to use
Sans Serif

Colors
f78f20
faa54b
ffffff

Requirements
Must have
• We'd like this project to incorporate an orange highlight colour (#FFA300), but otherwise be more or less, black and white. If you'd like to also add a primary colour in your design (outside of the orange and grayscale colours), we're happy to explore it!

NOTICE: At the top of the portfolio section, we'd like a full banner highlighted section for Kelpwarden (a SaaS platform owned and operated by BrambleForge).
Nice to have
• We want the website design to be more on the clean side, for example, look at the portfolio section from: https://www.quillandmarsh.co.uk/ (ignore the top banner).

We're also open to exploring bold designs, something like: https://ferret.net/

```html
<!DOCTYPE html>
<html lang="en">
<head>
<meta charset="utf-8">
<title>BrambleForge — Kelpwarden</title>
<link href="https://fonts.googleapis.com/css2?family=Poppins:wght@400;500;600;700;800&display=swap" rel="stylesheet">
<style>
:root{
  --orange:#f78f20;
  --orange-hi:#ffa300;
  --orange-soft:#faa54b;
  --ink:#3f3f3f;
  --text:#555;
  --grey-band:#f8f8f8;
  --footer:#4a4a4a;
  --footer-bar:#3e3e3e;
  --white:#fff;
}
*{margin:0;padding:0;box-sizing:border-box}
html,body{width:1200px;height:2297px;overflow:hidden}
body{position:relative;background:var(--white);font-family:'Poppins',sans-serif;color:var(--text)}
.abs{position:absolute}
.brand{font-family:'Poppins',sans-serif;font-weight:700;color:var(--ink);display:flex;align-items:center;gap:8px}
.brand .mark{width:22px;height:22px;background:var(--orange)}
.site-header .brand{left:89px;top:24px;font-size:26px}
.nav{left:432px;top:27px;display:flex;gap:26px;font-size:14px;color:var(--ink)}
.wave{width:48px;height:12px}
.hero-title{left:88px;top:236px;font-size:62px;line-height:62px;font-weight:800;color:var(--ink);letter-spacing:0.5px}
.hero-title .accent{color:var(--orange)}
.hero-sub{left:89px;top:455px;width:330px;font-size:16px;line-height:22px;color:var(--ink)}
.hero-circle{left:790px;top:214px;width:518px;height:518px;border-radius:50%;background:var(--orange-hi)}
.emblem{border-radius:24px;background:linear-gradient(145deg,var(--orange-soft),var(--orange));box-shadow:0 30px 60px rgba(0,0,0,.18)}
.band{left:0;top:668px;width:1200px;height:503px;background:var(--grey-band)}
.section-title{left:80px;top:908px;font-size:31px;font-weight:800;color:var(--ink)}
.bg-copy{left:469px;top:838px;width:590px;font-size:16px;line-height:26.7px;color:var(--text)}
.shot-card{left:78px;top:1237px;width:488px;height:305px;background:var(--white);border-radius:10px;box-shadow:0 25px 50px rgba(0,0,0,.12)}
.shot-card .dots{position:absolute;left:27px;top:13px;display:flex;gap:5px}
.shot-card .dots i{width:11px;height:11px;border-radius:50%;display:block}
.shot-screen{position:absolute;left:9px;top:34px;width:471px;height:262px;background:linear-gradient(90deg,#3d3d3d 0 11%,#eceff1 11%);border-radius:6px}
.avatar{left:532px;top:1506px;width:68px;height:68px;border-radius:50%;background:linear-gradient(135deg,#c9c4bd,#6a6460);border:3px solid var(--white)}
.dot-grid{left:38px;top:1511px;display:grid;grid-template-columns:repeat(4,10px);gap:11px 11px}
.dot-grid i{width:5px;height:5px;border-radius:50%;background:#f0396b;display:block}
.niche-copy{left:644px;top:1357px;width:470px;font-size:16px;line-height:26.7px}
.footer{left:0;top:1852px;width:1200px;height:388px;background:var(--footer)}
.footer-bar{left:0;top:2240px;width:1200px;height:57px;background:var(--footer-bar);color:var(--white);font-size:12px;font-weight:500;text-align:center;line-height:57px}
.cta-text{left:255px;top:1760px;font-size:37px;font-weight:800;color:var(--white)}
.cta-btn{left:757px;top:1757px;width:168px;height:52px;border-radius:26px;background:var(--white);color:var(--ink);font-weight:800;font-size:14px;text-align:center;line-height:52px}
.cta-line{left:342px;top:1738px;width:204px;height:2px;background:var(--white)}
.footer .brand{color:var(--white);left:128px;top:175px;font-size:38px;position:absolute}
.footer .brand .mark{width:30px;height:30px;background:var(--orange-hi)}
.socials{position:absolute;left:200px;top:228px;display:flex;gap:6px}
.socials i{width:36px;height:36px;border-radius:50%;background:#5a5a5a;display:block}
.col{position:absolute;top:124px;color:var(--white)}
.col h4{font-size:18px;font-weight:700;margin-bottom:12px}
.col li{list-style:none;font-size:14px;line-height:28.5px}
.contact-item{display:flex;gap:10px;font-size:14px;line-height:18px;margin-bottom:18px}
.contact-item svg{flex:none;margin-top:2px}
.to-top{left:1123px;top:2223px;width:41px;height:41px;border-radius:50%;background:var(--orange-hi)}
</style>
</head>
<body>

<header class="site-header">
  <div class="brand abs"><span class="mark"></span>BrambleForge</div>
  <nav class="nav abs">
    <span>Portfolio</span><span>Our Approach</span><span>Who We Serve</span><span>Testimonials</span><span>Executive Team</span><span>Contact Us</span>
  </nav>
</header>

<div class="band abs"></div>

<section class="hero">
  <div class="hero-circle abs"></div>
  <div class="emblem abs" style="left:660px;top:190px;width:360px;height:400px" role="img" aria-label="Large 3D brand emblem in orange"></div>
  <svg class="wave abs" style="left:89px;top:214px" viewBox="0 0 48 12"><path d="M2 8 q5-7 10 0 t10 0 t10 0 t10 0" fill="none" stroke="#c9c9c9" stroke-width="3" stroke-linecap="round"/></svg>
  <h1 class="hero-title abs"><span class="accent">BrambleForge</span><br>Kelpwarden is a<br>specialized</h1>
  <p class="hero-sub abs">BrambleForge Kelpwarden is a specialized construction SaaS solution</p>
</section>

<section class="background">
  <svg class="wave abs" style="left:84px;top:892px" viewBox="0 0 48 12"><path d="M2 8 q5-7 10 0 t10 0 t10 0 t10 0" fill="none" stroke="#c9c9c9" stroke-width="3" stroke-linecap="round"/></svg>
  <h2 class="section-title abs">Background</h2>
  <p class="bg-copy abs">As a tech entrepreneur and an Engineer who grew up in the construction industry, Darian saw a challenge around the construction tendering process, and created Kelpwarden to provide a simple, streamlined solution. Five years later and Kelpwarden has helped construction professionals tender thousands of projects, send out many millions of emails, and support hundreds of construction estimating professionals throughout North America.</p>
</section>

<section class="product">
  <div class="emblem abs" style="left:226px;top:1050px;width:192px;height:190px;box-shadow:none" role="img" aria-label="Small 3D brand emblem in orange"></div>
  <div class="shot-card abs">
    <div class="dots"><i style="background:#e94335"></i><i style="background:#f7b92b"></i><i style="background:#2fb94d"></i></div>
    <div class="shot-screen" role="img" aria-label="Kelpwarden app screen showing an email reporting table"></div>
  </div>
  <div class="avatar abs" role="img" aria-label="Portrait of a Kelpwarden user"></div>
  <div class="dot-grid abs">
    <i></i><i></i><i></i><i></i>
    <i></i><i></i><i></i><i></i>
    <i></i><i></i><i></i><i></i>
    <i></i><i></i><i></i><i></i>
    <i></i><i></i><i></i><i></i>
  </div>
  <p class="niche-copy abs">Our niche solution is known for its simplicity, reliability and fair privacy policy, where users own the contact list data that they use within the platform.</p>
</section>

<svg class="abs" style="left:0;top:1840px" width="1200" height="130" viewBox="0 0 1200 130">
  <polygon points="0,130 0,126 410,12 1200,12" fill="var(--footer)"/>
  <polygon points="0,128 410,12 430,12 0,135" fill="var(--orange-hi)"/>
  <polygon points="790,12 1200,118 1200,130 760,12" fill="var(--orange-hi)"/>
</svg>

<footer class="footer abs">
  <div class="brand"><span class="mark"></span>BrambleForge</div>
  <div class="socials"><i></i><i></i><i></i><i></i></div>
  <div class="col" style="left:501px"><h4>Quick Links</h4><ul><li>Portfolio</li><li>Our Approach</li><li>Who We Serve</li><li>Testimonials</li><li>Executive Team</li><li>Contact Us</li></ul></div>
  <div class="col" style="left:690px"><h4>Portfolio</h4><ul><li>Kelpwarden</li><li>Nimbo</li><li>CrateDeck</li><li>TileTrade</li><li>HeatSieve</li><li>EchoReply</li></ul></div>
  <div class="col" style="left:884px"><h4>Contact Us</h4>
    <div class="contact-item"><svg width="13" height="10" viewBox="0 0 13 10"><rect width="13" height="10" rx="1" fill="var(--orange-hi)"/><path d="M0 1 6.5 6 13 1" stroke="#4a4a4a" fill="none"/></svg><span>Email:<br>www.example.com</span></div>
    <div class="contact-item"><svg width="13" height="13" viewBox="0 0 24 24"><path d="M6.6 10.8a15 15 0 0 0 6.6 6.6l2.2-2.2a1 1 0 0 1 1-.25 11 11 0 0 0 3.6.6 1 1 0 0 1 1 1V20a1 1 0 0 1-1 1A17 17 0 0 1 3 4a1 1 0 0 1 1-1h3.5a1 1 0 0 1 1 1 11 11 0 0 0 .6 3.6 1 1 0 0 1-.25 1z" fill="var(--orange-hi)"/></svg><span>Phone:<br>(818) 123-4567</span></div>
    <div class="contact-item"><svg width="11" height="14" viewBox="0 0 24 32"><path d="M12 0a12 12 0 0 0-12 12c0 9 12 20 12 20s12-11 12-20A12 12 0 0 0 12 0zm0 17a5 5 0 1 1 0-10 5 5 0 0 1 0 10z" fill="var(--orange-hi)"/></svg><span>Office Location:<br>Some address line goes<br>here with city...</span></div>
  </div>
</footer>

<section class="cta">
  <svg class="abs" style="left:230px;top:1683px" width="736" height="170" viewBox="0 0 736 170">
    <path d="M18 34h688a30 30 0 0 1 30 30v88a18 18 0 0 1-18 18H18A18 18 0 0 1 0 152V52a18 18 0 0 1 18-18z" fill="#f2a313"/>
    <path d="M18 0h320q20 0 30 14l120 140q8 16-10 16H18A18 18 0 0 1 0 152V18A18 18 0 0 1 18 0z" fill="var(--orange-hi)"/>
    <circle cx="60" cy="45" r="15" fill="#fff"/><path d="M52 57 48 70 62 59z" fill="#fff"/>
    <path d="M70 34a14 14 0 0 1 4 24" stroke="#fff" stroke-width="3" fill="none"/>
  </svg>
  <div class="cta-line abs"></div>
  <div class="cta-text abs">Have a project in mind?</div>
  <div class="cta-btn abs">GET IN TOUCH</div>
</section>

<div class="footer-bar abs">© COPYRIGHT BRAMBLEFORGE 2021. ALL RIGHTS RESERVED</div>
<div class="to-top abs"><svg width="41" height="41" viewBox="0 0 41 41"><path d="M20.5 27V14M15 19l5.5-5.5L26 19" stroke="#fff" stroke-width="1.5" fill="none"/></svg></div>

</body>
</html>
```